Custom Cabinet Shop Needs a website design

Hi,
We need a website for a Custom Cabinet Shop and Cabinet parts manufacturing business.
The business has two sides to it. One side provides custom Kitchens, vanities, entertainment units, offices and what not to homeowners and contractors.
The 2nd side of the business provides built to order cabinet boxes and other parts required to put together a project to other cabinet shops, small contractors looking to install there own cabinets.
Website will need a Gallery to display work.
Color scheme to go well with logo.
current website is www.brambleoakcustomcabinets.com
being changed to www.brambleoak.ca
Logo Included in attached files.
Tagline "Joinery with Spirit"
Mission Statement "Our passion is to deliver inspired cabinetry solutions to suit all your needs, supported by our phenomenal star class customer service"
The website should convey quality and professionalism.
Thank you.
Homeowners/ Contractors
Entertainment

```html
<!DOCTYPE html>
<html lang="en">
<head>
<meta charset="utf-8">
<title>Brambleoak Custom Cabinets</title>
<link rel="stylesheet" href="https://fonts.googleapis.com/css2?family=Dosis:wght@600&family=Raleway:wght@400;500;600&display=swap">
<style>
:root{
  --orange:#f26122;
  --orange-dark:#d9501a;
  --page:#cfd1c9;
  --ink:#3b3b3b;
  --muted:#666;
  --rule:#a8a8a8;
  --footer:#161616;
  --footer-base:#050505;
  --footer-text:#b9b9b9;
  --date-dark:#3a3a3a;
  --amber:#f39214;
}
*{box-sizing:border-box;margin:0;padding:0}
html,body{width:1060px;height:1200px;overflow:hidden}
body{background:var(--page);font-family:"Raleway",sans-serif;color:var(--ink);position:relative}
.page{position:absolute;left:97px;top:0;width:866px;height:910px;background:#fff}
.topbar{position:absolute;right:12px;top:11px;font-size:12px;display:flex;align-items:center;gap:14px;color:#555}
.topbar .hotline{font-weight:600;letter-spacing:.3px}
.topbar .phone{color:var(--orange);font-weight:600;font-size:14px}
.dot{display:inline-flex;width:12px;height:12px;border-radius:50%;background:var(--orange);color:#fff;font-size:9px;align-items:center;justify-content:center;margin-left:4px;vertical-align:-1px}
.navband{position:absolute;left:-9px;top:57px;width:882px;height:47px;background:var(--orange)}
.brand{position:absolute;left:0;top:39px;width:270px;height:81px;background:#fff;clip-path:polygon(0 0,100% 0,78% 100%,0 100%);z-index:3}
.brand-name{position:absolute;left:14px;top:28px;display:flex;align-items:center;gap:8px;font-weight:600;font-size:19px;color:#222;letter-spacing:.5px}
.brand-name i,.foot-brand i{display:block;width:14px;height:14px;background:var(--orange)}
.nav{position:absolute;left:295px;top:57px;height:47px;display:flex;z-index:4}
.nav a{color:#fff;text-decoration:none;font-size:13px;font-weight:500;line-height:47px;padding:0 30px;border-left:1px solid var(--orange-dark);transform:skewX(-18deg)}
.nav a span{display:inline-block;transform:skewX(18deg)}
.nav a:first-child{border-left:none}
.hero{position:absolute;left:0;top:104px;width:866px;height:363px;background:linear-gradient(160deg,#3a4152 0%,#2a2f3b 35%,#6b4a34 70%,#3a2a20 100%)}
.hero h1{position:absolute;left:0;right:0;top:143px;text-align:center;font-family:"Dosis",sans-serif;font-weight:600;font-size:46px;color:#fff;letter-spacing:1px}
.arrow{position:absolute;top:152px;width:34px;height:44px;background:#fff;display:flex;align-items:center;justify-content:center}
.arrow.prev{left:0;border-radius:0 4px 4px 0}
.arrow.next{right:0;border-radius:4px 0 0 4px}
.heading{position:absolute;height:28px;border-bottom:2px solid var(--rule);font-size:19px;font-weight:600;padding-left:20px}
.heading::before{content:"";position:absolute;left:5px;top:-2px;width:2px;height:32px;background:var(--orange);transform:skewX(-20deg)}
.heading b{color:var(--orange);font-weight:600}
.gal-ctrl{position:absolute;right:0;top:0;display:flex;gap:2px}
.gal-ctrl span{width:20px;height:16px;background:var(--orange);transform:skewX(-18deg)}
.thumbs{position:absolute;left:18px;top:547px;display:flex;gap:15px}
.thumb{width:198px;height:105px;position:relative}
.t1{background:linear-gradient(135deg,#e9e4dc,#7d5a42)}
.t2{background:linear-gradient(135deg,#4a4a4a,#1f1f1f)}
.t3{background:linear-gradient(135deg,#f0ede6,#2b2521)}
.t4{background:linear-gradient(135deg,#cfd8d9,#6b4b33)}
.tag{position:absolute;left:-8px;top:40px;background:var(--orange);color:#fff;font-family:"Dosis",sans-serif;font-size:20px;padding:2px 20px 2px 10px;clip-path:polygon(0 0,100% 0,88% 100%,0 100%)}
.about{position:absolute;left:23px;top:733px;width:512px;font-size:13.2px;line-height:21.2px;color:#555}
.news{position:absolute;left:564px;width:285px}
.news-item{position:absolute;left:0;width:285px}
.date{position:absolute;left:0;top:0;width:48px}
.date .d{height:30px;background:var(--amber);color:#fff;text-align:center;font-size:18px;line-height:30px;position:relative}
.date .d::after{content:"";position:absolute;right:-6px;top:10px;border:5px solid transparent;border-left-color:var(--amber);border-right:0}
.date .m{height:27px;background:var(--date-dark);color:#fff;text-align:center;font-size:11px;line-height:27px}
.news-item h3{position:absolute;left:63px;top:-2px;font-size:16px;font-weight:500;white-space:nowrap}
.news-item p{position:absolute;left:63px;top:22px;font-size:12.5px;line-height:19px;color:#666;width:230px}
.footer{position:absolute;left:96px;top:910px;width:869px;height:238px;background:var(--footer);color:var(--footer-text)}
.fcol{position:absolute;top:32px}
.fcol h4{color:#fff;font-weight:500;font-size:15px;padding-bottom:12px;border-bottom:1px solid #444}
.fcol ul{list-style:none;margin-top:17px}
.fcol li{font-size:12.5px;line-height:23px}
.fcol li::before{content:"›";margin-right:6px;color:#888}
.contact{font-size:12.5px;line-height:19.5px}
.crow{display:flex;gap:10px;align-items:flex-start}
.bigphone{font-size:16px;color:#ddd}
.foot-brand{position:absolute;left:735px;top:116px;display:flex;align-items:center;gap:8px;color:#fff;font-weight:600;font-size:17px;letter-spacing:.5px}
.base{position:absolute;left:96px;top:1148px;width:869px;height:52px;background:var(--footer-base);color:#ddd;font-size:12.5px}
.base .copy{position:absolute;left:15px;top:22px}
.base .links{position:absolute;right:14px;top:22px;display:flex;gap:14px}
</style>
</head>
<body>
<div class="page">
  <div class="topbar">
    <span>Online support<span class="dot">?</span></span>
    <span class="hotline">HOTLINE <span class="dot" style="border-radius:2px">✆</span></span>
    <span class="phone">403-555-0142</span>
  </div>
  <div class="navband"></div>
  <div class="brand"><div class="brand-name"><i></i>BRAMBLEOAK</div></div>
  <nav class="nav">
    <a href="#"><span>HOME</span></a>
    <a href="#"><span>GALLERY</span></a>
    <a href="#"><span>SERVICES</span></a>
    <a href="#"><span>WARRANTY</span></a>
    <a href="#"><span>CONTACT</span></a>
  </nav>
  <section class="hero" role="img" aria-label="Basement bar with live-edge wood counter, stone base, stools and dark cabinetry">
    <h1>JOINERY WITH SPIRIT</h1>
    <div class="arrow prev"><svg width="12" height="20"><path d="M10 2 2 10l8 8" stroke="#666" stroke-width="2" fill="none"/></svg></div>
    <div class="arrow next"><svg width="12" height="20"><path d="M2 2l8 8-8 8" stroke="#666" stroke-width="2" fill="none"/></svg></div>
  </section>

  <div class="heading" style="left:21px;top:501px;width:827px"><b>OUR</b> GALLERY
    <div class="gal-ctrl"><span></span><span></span></div>
  </div>
  <div class="thumbs" style="left:18px;top:547px">
    <div class="thumb t1" role="img" aria-label="Bright kitchen with island and pendant light"></div>
    <div class="thumb t2" role="img" aria-label="Dark modern kitchen"><span class="tag">Residential</span></div>
    <div class="thumb t3" role="img" aria-label="Dark entertainment wall unit"></div>
    <div class="thumb t4" role="img" aria-label="Dining nook with bench seating"></div>
  </div>

  <div class="heading" style="left:22px;top:687px;width:513px"><b>WHO</b> WE ARE</div>
  <p class="about">Lorem Ipsum is simply dummy text of the printing and typesetting industry. Lorem Ipsum has been the industry's standard dummy text ever since the 1500s, when an unknown printer took a galley of type and scrambled it to make a type specimen book. It has survived not only five centuries, but also the leap into electronic typesetting, remaining essentially unchanged. It was popularised in the 1960s with the release of Letraset sheets containing Lorem Ipsum passages, and more recently with desktop publishing software like Aldus PageMaker including versions of Lorem Ipsum.</p>

  <div class="heading" style="left:561px;top:687px;width:288px"><b>LATEST</b> NEWS</div>
  <div class="news" style="top:739px">
    <div class="news-item" style="top:0">
      <div class="date"><div class="d">01</div><div class="m">MAR</div></div>
      <h3>Lorem Ipsum is simply</h3>
      <p>Lorem Ipsum is simply dummy text of the printing and typesetting industry.</p>
    </div>
    <div class="news-item" style="top:77px">
      <div class="date"><div class="d">01</div><div class="m">MAR</div></div>
      <h3>Lorem Ipsum is simply</h3>
      <p>Lorem Ipsum is simply dummy text of the printing and typesetting industry.</p>
    </div>
  </div>
</div>

<footer class="footer">
  <div class="fcol" style="left:20px;width:157px"><h4>Who We Are</h4>
    <ul><li>Home</li><li>Gallery</li><li>Services</li><li>Warranty</li><li>Contact</li></ul></div>
  <div class="fcol" style="left:193px;width:193px"><h4>Our Services</h4>
    <ul><li>Lorem Ipsum Dolor Sit Amet</li><li>Typesetting Industry</li><li>Have been Sent in Lorem</li><li>Services Which Done</li><li>Inside Vehicula Quis</li></ul></div>
  <div class="fcol" style="left:420px;width:193px"><h4>Contact Us</h4>
    <div class="contact" style="margin-top:14px">
      <div class="crow"><svg width="14" height="18" viewBox="0 0 14 18"><path d="M7 0a7 7 0 0 0-7 7c0 5 7 11 7 11s7-6 7-11a7 7 0 0 0-7-7z" fill="#777"/><circle cx="7" cy="7" r="2.5" fill="#161616"/></svg><span>4120 Range Road 91<br>Cedar Hollow, Alberta<br>T0X 2B4</span></div>
      <div class="crow" style="margin-top:2px"><svg width="16" height="18" viewBox="0 0 16 18"><path d="M3 1l3 4-2 2c1 3 3 5 6 6l2-2 4 3-2 3C7 17 0 10 1 3z" fill="#777"/></svg><span class="bigphone">403-555-0187</span></div>
      <div class="crow" style="margin-top:12px;white-space:nowrap"><svg width="18" height="12" viewBox="0 0 18 12"><rect x="0.5" y="0.5" width="17" height="11" fill="none" stroke="#777"/><path d="M1 1l8 6 8-6" stroke="#777" fill="none"/></svg><span>sales@brambleoakcustomcabinets.com</span></div>
    </div>
  </div>
  <div class="foot-brand"><i></i>BRAMBLEOAK</div>
</footer>
<div class="base">
  <span class="copy">copyright©2015.Bramble Oak Cabinet. All Rights Reserved</span>
  <span class="links"><span>Privacy Policy</span><span>|</span><span>Terms &amp; Conditions</span></span>
</div>
</body>
</html>
```